Zing Webcomic

A simple signup landing page and blog design for an upcoming webcomic. I am mostly looking for a flat UI with a simple color scheme. I want to showcase a large background image and the comic title image. I have all the technicals figured out (I am a web developer by trade), so all I need now is a solid design I like.

The signup for should only have one field (email) and have text above it, and smaller text below it.

The blog, I am thinking, should be in the style of comic book pages. The home page would be blocks with large white outlines, with the article pages being an extension of that. As I stated before, should be fairly minimalist, but fun. Also, no sidebar or ads, IE single column. I have attached a simple mockup/layout of the blog to give a general idea of what I am going for.

I have attached the Logo and Background art (uncolored) for reference. Don't worry about the background image blending in, I can take care of that when the design is implemented. I will be focusing on layout and overall look, not necessarily readability (which I can fix).

~Please DO NOT take these examples literally. I will describe what I like about each example.~

Signup pages:
http://example-plaza.test/landing-page-type-photo/
http://www.lanternhop.test/showcase/website-design/814/10-most-beautiful-landing-pages-in-minimalist-style
http://quillnest.test/47-modern-landing-pages-showcasing-inspirational-web-design/
Great examples of minimalist design. However, instead of text or other content, there should be a simple signup form, as described above. Also think a lot more "playful" rather than super professional.

Blog:
http://vrakk.test/
Awesome example of a single column, minimal design. Needs to be more "comicbook style" though.
http://tidyrows.test/
Another good example of minimal design blog.
http://makerbarn.test/wp-content/uploads/res-blogs-5.jpg
I like the timeline feel here. Combine that with a comic book page kind of thing, and I think you have a winner.

Actual webcomic landing (not required):
http://www.lunarfoxpanels.test/comic.php?date=20021104#.U90ysYBdUvU
I like the navigation. It makes the atmosphere nice for the comic. The page layout itself is WAY too busy.
http://www.dime-galaxy.test/comic/
Fairly common webcomic, but their navigation and page layout is nice.
http://qvmp.test/936/
Another common webcomic. The simple page layout makes it easy for people to get started I think.

So there you have it. I will try my best to keep updating and adding to the description. If you have any questions, please don't hesitate to ask.
Updates

Hey Guys, I am really appreciating all the effort you have been putting in. I am amazed to see all the awesome designs and all the care taken with the project. I am just writing everyone to let you know that I have uploaded a simple layout/wireframe of the blog, to give an idea of what I am going for. Can't wait to see how things progress, and good luck to everyone!

Industry/Entity Type

Trade

Font styles to use
Sans Serif

Requirements
Must have
• Must showcase a large background image (does not have to cover the entire background). Should be a flat UI as well. Should be mostly neutral with splashes of blue or purple. Social links should also be somewhere (twitter, facebook, etc.).
Nice to have
• I am thinking something with rounded boxes, but I can live without them. A more "fun" design as opposed to more professional is definitely nice to have.

If you would like to try a stab at the actual comic page display and navigation, you are welcome to submit something. It should not be a main priority though.

Being responsive is not a requirement, but it would be nice to have.
Should not have
• A billion links in the navigation or look too busy.
No sidebar or advertisements. Should be a clean design.

```html
<!DOCTYPE html>
<html lang="en">
<head>
<meta charset="utf-8">
<title>Zing Webcomic — Sign Up</title>
<link rel="stylesheet" href="https://fonts.googleapis.com/css2?family=Raleway:wght@400;600;700;800&family=Noto+Serif:wght@400&display=swap">
<style>
  :root {
    --purple: #7541b3;
    --purple-deep: #6a37a6;
    --purple-light: #8150bd;
    --white: #ffffff;
    --cyan: #00bcf2;
    --icon-fill: #e4dcef;
    --icon-ink: #5a3090;
    --field-text: #8a8a8a;
  }
  * { box-sizing: border-box; margin: 0; padding: 0; }
  html, body { width: 1200px; height: 676px; overflow: hidden; }
  body {
    position: relative;
    background: var(--purple);
    font-family: "Raleway", Arial, sans-serif;
    color: var(--white);
  }
  .hero-art {
    position: absolute; inset: 0;
    background:
      radial-gradient(ellipse at 25% 30%, var(--purple-deep) 0%, transparent 55%),
      radial-gradient(ellipse at 80% 75%, var(--purple-deep) 0%, transparent 50%),
      linear-gradient(180deg, var(--purple-light) 0%, var(--purple) 60%, var(--purple-deep) 100%);
    opacity: 0.9;
  }
  .site-header {
    position: absolute; left: 164px; right: 162px; top: 16px;
    display: flex; justify-content: space-between; align-items: flex-start;
  }
  .brand {
    margin-top: 12px;
    font-family: "Raleway", Arial, sans-serif;
    font-weight: 800; font-size: 46px; line-height: 1;
    color: var(--white); letter-spacing: 1px;
  }
  .contact-button {
    display: inline-block;
    width: 126px; height: 40px; line-height: 36px;
    border: 2px solid var(--white); border-radius: 3px;
    text-align: center; text-decoration: none;
    color: var(--white); font-weight: 600; font-size: 16px;
  }
  .signup {
    position: absolute; left: 0; right: 0; top: 253px;
    text-align: center;
  }
  .signup-headline {
    font-family: "Noto Serif", Georgia, serif;
    font-weight: 400; font-size: 26px; line-height: 46px;
  }
  .signup-form {
    display: flex; width: 450px; height: 48px;
    margin: 28px 0 0 calc(50% - 236px);
  }
  .signup-email {
    flex: 1; border: 0; border-radius: 3px 0 0 3px;
    padding: 0 15px; font-family: inherit; font-size: 12px;
    color: var(--field-text); background: var(--white);
  }
  .signup-email::placeholder { color: var(--field-text); }
  .signup-send {
    width: 130px; border: 0; border-radius: 0 3px 3px 0;
    background: var(--cyan); color: var(--white);
    font-family: inherit; font-weight: 700; font-size: 15px;
  }
  .site-footer {
    position: absolute; left: 0; right: 0; top: 617px;
    text-align: center;
  }
  .social-links { display: flex; justify-content: center; gap: 8px; list-style: none; }
  .social-links a {
    display: block; width: 25px; height: 25px; border-radius: 50%;
    background: var(--icon-fill); border: 2px solid var(--icon-ink);
  }
  .copyright { margin-top: 13px; font-size: 10px; }
</style>
</head>
<body>
  <div class="hero-art" role="img" aria-label="Faint line-art background of the comic's city, a dragon and heroes"></div>

  <header class="site-header">
    <div class="brand">Zing</div>
    <a class="contact-button" href="#contact">CONTACT US</a>
  </header>

  <main class="signup">
    <h1 class="signup-headline">Lorem ipsum dolor sit amet, consectetur adipisicing elit,<br>sed do eiusmod tempor incididunt ut labore</h1>
    <form class="signup-form">
      <input class="signup-email" type="email" placeholder="Enter your email">
      <button class="signup-send" type="submit">SEND</button>
    </form>
  </main>

  <footer class="site-footer">
    <ul class="social-links">
      <li><a href="#" aria-label="Social profile 1"></a></li>
      <li><a href="#" aria-label="Social profile 2"></a></li>
      <li><a href="#" aria-label="Social profile 3"></a></li>
      <li><a href="#" aria-label="Social profile 4"></a></li>
      <li><a href="#" aria-label="Social profile 5"></a></li>
      <li><a href="#" aria-label="Video channel"></a></li>
    </ul>
    <p class="copyright">Copyright © 2014 Zing Webcomic All rights reserved.</p>
  </footer>
</body>
</html>
```